Business Card Design

New business card design

Target Market(s)

Residential & Commercial Property Managers

Industry/Entity Type

Plumbing Services

Contact Information for Business Card

Name - Rowan Keddle, title - Director, Phone Number - 0431 286 517, email - rowan@tbk-plumbing.com.au, Company ABN - 73 215 904 386,

Font styles to use
Sans Serif

Colors
0054AA
0677BA
7BADD7
CADEEF
E8F1F8

```html
<!DOCTYPE html>
<html lang="en">
<head>
<meta charset="utf-8">
<title>TBK Plumbing Services – Business Card</title>
<link href="https://fonts.googleapis.com/css2?family=Montserrat:wght@400;700&display=swap" rel="stylesheet">
<style>
  :root {
    --page-bg: #2a2c2f;
    --card-white: #ffffff;
    --ink-navy: #1d2228;
    --accent-blue: #29a8e0;
  }
  * { margin: 0; padding: 0; box-sizing: border-box; }
  html, body {
    width: 1200px; height: 880px; overflow: hidden;
    background: var(--page-bg);
    font-family: "Montserrat", sans-serif;
  }
  .canvas {
    position: relative; width: 1200px; height: 880px;
    display: flex; flex-direction: column; align-items: center; justify-content: center; gap: 40px;
  }
  .card {
    position: relative; width: 680px; height: 390px;
    background: var(--card-white); border-radius: 26px; overflow: hidden;
  }
  .brand {
    position: absolute; display: flex; align-items: center; gap: 12px;
    color: var(--ink-navy); font-weight: 400; white-space: nowrap; z-index: 2;
  }
  .brand-dot {
    width: 0.7em; height: 0.7em; border-radius: 50%; background: var(--accent-blue); flex: none;
  }
  .card-front .brand { left: 50%; top: 50%; transform: translate(-50%, -50%); font-size: 44px; letter-spacing: 1px; }
  .card-back .brand { left: 40px; top: 100px; font-size: 27px; letter-spacing: 0.5px; }
  .wave { position: absolute; inset: 0; width: 100%; height: 100%; z-index: 1; }
  .name-block { position: absolute; right: 40px; top: 22px; text-align: right; z-index: 2; }
  .name { color: var(--accent-blue); font-weight: 700; font-size: 30px; line-height: 1.1; }
  .title { color: var(--ink-navy); font-size: 17px; margin-top: 2px; }
  .name-bar { position: absolute; right: 0; top: 22px; width: 14px; height: 60px; background: var(--accent-blue); z-index: 2; }
  .contact {
    position: absolute; right: 30px; bottom: 34px; text-align: right; z-index: 2;
    color: var(--card-white); font-size: 17px; line-height: 1.45;
  }
  .contact .abn { margin-bottom: 16px; }
  .contact-line { display: flex; justify-content: flex-end; align-items: center; gap: 8px; }
  .contact-line svg { width: 16px; height: 16px; flex: none; }
</style>
</head>
<body>
<main class="canvas">
  <section class="card card-front">
    <div class="brand"><span class="brand-dot"></span>TBK Plumbing Services</div>
  </section>

  <section class="card card-back">
    <svg class="wave" viewBox="0 0 680 390" aria-hidden="true">
      <path d="M0,350 C220,335 300,310 370,220 C440,130 540,118 680,112 L680,390 L0,390 Z" fill="#29a8e0"/>
      <path d="M0,362 C224,346 308,320 378,230 C446,140 545,128 680,122 L680,390 L0,390 Z" fill="#ffffff"/>
      <path d="M0,367 C226,351 312,325 382,235 C450,145 548,133 680,127 L680,390 L0,390 Z" fill="#1d2228"/>
    </svg>
    <div class="brand"><span class="brand-dot"></span>TBK Plumbing Services</div>
    <div class="name-block">
      <div class="name">Rowan Keddle</div>
      <div class="title">Director</div>
    </div>
    <div class="name-bar"></div>
    <div class="contact">
      <div class="abn">Company ABN<br>- 73 215 904 386</div>
      <div class="contact-line">0431 286 517
        <svg viewBox="0 0 24 24"><path fill="#29a8e0" d="M6.6 10.8a15 15 0 0 0 6.6 6.6l2.2-2.2c.3-.3.7-.4 1-.2 1.1.4 2.3.6 3.6.6.6 0 1 .4 1 1V20c0 .6-.4 1-1 1A17 17 0 0 1 3 4c0-.6.4-1 1-1h3.5c.6 0 1 .4 1 1 0 1.3.2 2.5.6 3.6.1.3 0 .7-.2 1z"/></svg>
      </div>
      <div class="contact-line">rowan@tbk-plumbing.com.au
        <svg viewBox="0 0 24 24"><path fill="#29a8e0" d="M3 5h18c.6 0 1 .4 1 1v12c0 .6-.4 1-1 1H3c-.6 0-1-.4-1-1V6c0-.6.4-1 1-1zm9 7.5L20 7H4z"/></svg>
      </div>
    </div>
  </section>
</main>
</body>
</html>
```